Interval Timer App

Need to have design for the attached wireframe. Similar app can be found here: https://shop.lumaverse.net/store/apps/details?id=cc.quillfern.pulseclock

```html
<!DOCTYPE html>
<html lang="en">
<head>
<meta charset="UTF-8">
<title>Interval Timer</title>
<link href="https://fonts.googleapis.com/css2?family=Nunito+Sans:wght@400;600;700&display=swap" rel="stylesheet">
<style>
  :root {
    --bg-top: #94f48c;
    --bg-bottom: #0ae06f;
    --card: #ffffff;
    --ink: #22212b;
    --accent: #1a7fe0;
    --track: #ffffff;
    --shadow: rgba(0, 0, 0, 0.18);
  }
  * { margin: 0; padding: 0; box-sizing: border-box; }
  html, body { width: 675px; height: 1200px; overflow: hidden; }
  body {
    position: relative;
    font-family: "Nunito Sans", "Open Sans", sans-serif;
    background: linear-gradient(160deg, var(--bg-top) 0%, var(--bg-bottom) 100%);
    color: var(--ink);
  }
  .back-button {
    position: absolute; left: 28px; top: 38px; width: 30px; height: 36px;
  }
  .set-progress {
    position: absolute; left: 195px; top: 166px; width: 285px; height: 60px;
  }
  .set-label {
    text-align: center; font-size: 21px; font-weight: 600; letter-spacing: 0.5px;
    padding-left: 0; width: 250px; margin-left: 0;
  }
  .set-track {
    position: absolute; left: 0; top: 50px; width: 285px; height: 4px;
    background: var(--track); border-radius: 2px;
  }
  .set-fill {
    position: absolute; left: 0; top: 0; width: 124px; height: 4px;
    background: var(--accent); border-radius: 2px;
  }
  .set-knob {
    position: absolute; left: 113px; top: -10px; width: 24px; height: 24px;
    border-radius: 50%; background: #fff; border: 4px solid var(--accent);
  }
  .timer-card {
    position: absolute; left: 30px; top: 281px; width: 615px; height: 638px;
    background: var(--card); border-radius: 15px;
  }
  .phase-title {
    position: absolute; left: 0; right: 0; top: 45px; text-align: center;
    font-size: 41px; font-weight: 400;
  }
  .progress-ring { position: absolute; left: 0; top: 0; }
  .time-remaining {
    position: absolute; left: 0; width: 608px; top: 274px; text-align: center;
    font-size: 88px; font-weight: 700; color: var(--accent); line-height: 1;
  }
  .round-button {
    position: absolute; top: 516px; width: 102px; height: 102px; border-radius: 50%;
    background: #fff; box-shadow: 0 2px 8px var(--shadow);
    display: flex; align-items: center; justify-content: center;
  }
  .reset-button { left: 18px; }
  .pause-button { left: 493px; }
</style>
</head>
<body>
  <svg class="back-button" viewBox="0 0 30 36" aria-label="Back">
    <polyline points="22,4 8,18 22,32" fill="none" stroke="#1a7fe0" stroke-width="4" stroke-linecap="round" stroke-linejoin="round"/>
  </svg>

  <div class="set-progress">
    <div class="set-label">SET 1</div>
    <div class="set-track">
      <div class="set-fill"></div>
      <div class="set-knob"></div>
    </div>
  </div>

  <main class="timer-card">
    <h1 class="phase-title">Work time!</h1>
    <svg class="progress-ring" width="615" height="638" viewBox="0 0 615 638">
      <path d="M 300 171 A 158 158 0 0 1 308 485" fill="none" stroke="#22212b" stroke-width="5" stroke-linecap="round"/>
      <circle cx="308" cy="484" r="14" fill="#1a7fe0"/>
    </svg>
    <div class="time-remaining">1:45</div>

    <div class="round-button reset-button" aria-label="Restart">
      <svg width="52" height="52" viewBox="0 0 52 52">
        <path d="M 16 40 A 17 17 0 1 1 32 42" fill="none" stroke="#1a7fe0" stroke-width="4" stroke-linecap="round"/>
        <polyline points="22,34 16,40 23,46" fill="none" stroke="#1a7fe0" stroke-width="4" stroke-linecap="round" stroke-linejoin="round"/>
      </svg>
    </div>
    <div class="round-button pause-button" aria-label="Pause">
      <svg width="40" height="40" viewBox="0 0 40 40">
        <line x1="12" y1="8" x2="12" y2="32" stroke="#1a7fe0" stroke-width="4" stroke-linecap="round"/>
        <line x1="28" y1="8" x2="28" y2="32" stroke="#1a7fe0" stroke-width="4" stroke-linecap="round"/>
      </svg>
    </div>
  </main>
</body>
</html>
```